New Bicycle shop business card

Hi!
I'm looking for a business card for my new proffesional bike mechanics shop. This shop is only for fixing broken bikes and not selling bikes.
Peferbly a modern and sleek and modern design.
Colors: black, grey, red, white
Information:
Name: Rijwielwerkplaats Vanhoutte
Shop owner: Bart Vanhoutte & Marieke Segers
Website: www.rijwielwerkplaats-vanhoutte.be
Email: info@rijwielwerkplaats-vanhoutte.be
Phone number: +32471902368
Street adres: Kerkweg 46
9940 Bellebeke
Slogan/shop information: Herstellingen van alle merken.
Logo: see files.
Target Market(s)
People who seek a mechanic to fix or upgrade their bikes.
Contact Information for Business Card
Information:
Website: info@rijwielwerkplaats-vanhoutte.be
9940 Bellebeke
Logo: see files.

```html
<!DOCTYPE html>
<html lang="nl">
<head>
<meta charset="utf-8">
<title>Rijwielwerkplaats Vanhoutte – Visitekaartje</title>
<link href="https://fonts.googleapis.com/css2?family=Montserrat:wght@700&family=Roboto:wght@400;500&display=swap" rel="stylesheet">
<style>
  :root {
    --backdrop: #3a3a3c;
    --card: #1f1f21;
    --white: #ffffff;
    --red: #e02a3a;
    --grey: #8c9196;
    --muted: #d9d9d9;
  }
  * { margin: 0; padding: 0; box-sizing: border-box; }
  html, body {
    width: 799px; height: 1200px; overflow: hidden;
    background: var(--backdrop);
    font-family: "Roboto", Arial, sans-serif;
  }
  .sheet {
    position: relative; width: 799px; height: 1200px;
    display: flex; flex-direction: column; align-items: center; justify-content: center;
    gap: 90px;
  }
  .card {
    position: relative; width: 600px; height: 350px;
    background: var(--card); border-radius: 26px; overflow: hidden;
    box-shadow: 0 14px 30px rgba(0,0,0,0.45);
  }

  /* front */
  .card-front {
    display: flex; flex-direction: column; align-items: center; justify-content: center;
  }
  .brand-name {
    font-family: "Montserrat", Arial, sans-serif; font-weight: 700;
    color: var(--white); text-align: center; line-height: 1.15;
  }
  .card-front .brand-name { font-size: 30px; letter-spacing: 2px; }
  .card-front .brand-name span { display: block; letter-spacing: 10px; }
  .website {
    margin-top: 34px; color: var(--white); font-size: 17px; letter-spacing: 0.3px;
  }
  .website .accent { color: var(--red); }

  /* back */
  .card-back .brand-name {
    position: absolute; left: 36px; top: 32px; text-align: left;
    font-size: 20px; letter-spacing: 1px;
  }
  .card-back .brand-name span { display: block; letter-spacing: 7px; }
  .person { position: absolute; left: 36px; top: 112px; }
  .person-name { color: var(--red); font-family: "Montserrat", Arial, sans-serif; font-weight: 700; font-size: 19px; letter-spacing: 0.5px; }
  .person-role { color: var(--muted); font-size: 13px; margin-top: 2px; }
  .contact-list { position: absolute; left: 36px; top: 190px; list-style: none; }
  .contact-list li {
    display: flex; align-items: center; gap: 10px;
    color: var(--white); font-size: 14px; line-height: 24px;
  }
  .contact-list svg { width: 13px; height: 13px; fill: var(--red); flex: none; }
  .address { color: var(--white); font-size: 14px; position: absolute; left: 36px; top: 292px; }
  .accent-block {
    position: absolute; right: 0; top: 110px; width: 190px; height: 240px;
    background: var(--red);
  }
</style>
</head>
<body>
<main class="sheet">
  <section class="card card-front" aria-label="Voorkant visitekaartje">
    <h1 class="brand-name">RIJWIELWERKPLAATS<span>VANHOUTTE</span></h1>
    <p class="website">www.rijwielwerkplaats-<span class="accent">vanhoutte</span>.be</p>
  </section>

  <section class="card card-back" aria-label="Achterkant visitekaartje">
    <h2 class="brand-name">RIJWIELWERKPLAATS<span>VANHOUTTE</span></h2>
    <div class="person">
      <p class="person-name">MARIEKE SEGERS</p>
      <p class="person-role">Owner</p>
    </div>
    <ul class="contact-list">
      <li>
        <svg viewBox="0 0 24 24" aria-hidden="true"><path d="M6.6 10.8a15.1 15.1 0 0 0 6.6 6.6l2.2-2.2c.3-.3.7-.4 1-.2 1.1.4 2.3.6 3.6.6.6 0 1 .4 1 1V20c0 .6-.4 1-1 1C10.6 21 3 13.4 3 4c0-.6.4-1 1-1h3.5c.6 0 1 .4 1 1 0 1.3.2 2.5.6 3.6.1.3 0 .7-.2 1z"/></svg>
        +32471902368
      </li>
      <li>
        <svg viewBox="0 0 24 24" aria-hidden="true"><path d="M12 2a10 10 0 1 0 0 20 10 10 0 0 0 0-20zm6.9 6h-3a15.6 15.6 0 0 0-1.3-3.6A8 8 0 0 1 18.9 8zM12 4c.8 1.2 1.5 2.5 1.9 4h-3.8c.4-1.5 1.1-2.8 1.9-4zM4.3 14a8 8 0 0 1 0-4h3.4a16 16 0 0 0 0 4zm.8 2h3a15.6 15.6 0 0 0 1.3 3.6A8 8 0 0 1 5.1 16zm3-8h-3a8 8 0 0 1 4.3-3.6C8.8 5.5 8.4 6.7 8.1 8zM12 20c-.8-1.2-1.5-2.5-1.9-4h3.8c-.4 1.5-1.1 2.8-1.9 4zm2.3-6H9.7a14.700 14.700 0 0 1 0-4h4.6a14.700 14.700 0 0 1 0 4zm.3 5.6c.6-1.1 1-2.3 1.3-3.6h3a8 8 0 0 1-4.3 3.6zm1.7-5.6a16 16 0 0 0 0-4h3.4a8 8 0 0 1 0 4z"/></svg>
        www.rijwielwerkplaats-vanhoutte.be
      </li>
      <li>
        <svg viewBox="0 0 24 24" aria-hidden="true"><path d="M2 5h20v14H2zm2 2v.5l8 5 8-5V7zm0 2.9V17h16V9.9l-8 5z"/></svg>
        info@rijwielwerkplaats-vanhoutte.be
      </li>
    </ul>
    <p class="address">Kerkweg 46 9940 Bellebeke</p>
    <div class="accent-block" aria-hidden="true"></div>
  </section>
</main>
</body>
</html>
```